Business Card Design

Online clothing womens clothing store, I sell my clothing online and at the markets.

i would like the attached picture on the front of the card and the contact information on the back.

Industry/Entity Type

Business

Contact Information for Business Card

Marlow Thread
Karen Whitfield
(Instagram symbol) _marlow_thread_
(Facebook symbol) www.fakebookexample.com/marlowthreadau/

W : www.marlowthread.example.au
E : info@marlowthread.example.au
P : 0498716204

```html
<!DOCTYPE html>
<html lang="en">
<head>
<meta charset="utf-8">
<title>Marlow Thread – Business Card</title>
<link rel="stylesheet" href="https://fonts.googleapis.com/css2?family=Josefin+Sans:wght@300;400&family=Oswald:wght@500&family=Arimo:wght@400&display=swap">
<style>
  :root {
    --page-bg: #d9d9d9;
    --card-white: #f4f4f4;
    --card-black: #050505;
    --band-grey: #9a9a9a;
    --band-light: #c9c9c9;
    --ink: #111111;
    --paper-text: #f2f2f2;
    --photo-light: #e3e7e8;
    --photo-mid: #aab4b9;
    --photo-dark: #5d5a5e;
  }
  html, body {
    margin: 0;
    padding: 0;
    width: 1200px;
    height: 864px;
    overflow: hidden;
    background: var(--page-bg);
  }
  .canvas {
    position: relative;
    width: 1200px;
    height: 864px;
    display: flex;
    align-items: center;
    justify-content: center;
    gap: 40px;
  }
  .card {
    position: relative;
    width: 540px;
    height: 309px;
    overflow: hidden;
    box-shadow: 0 6px 18px rgba(0,0,0,0.18);
  }

  /* Contact side */
  .card--contact { background: var(--card-white); }
  .card__waves { position: absolute; inset: 0; }
  .brand-name {
    position: absolute;
    top: 46px;
    left: 0;
    width: 100%;
    text-align: center;
    margin: 0;
    font-family: "Josefin Sans", sans-serif;
    font-weight: 400;
    font-size: 28px;
    letter-spacing: 9px;
    color: var(--ink);
    text-transform: uppercase;
  }
  .holder-name {
    position: absolute;
    top: 184px;
    left: 34px;
    margin: 0;
    font-family: "Josefin Sans", sans-serif;
    font-weight: 300;
    font-size: 18px;
    letter-spacing: 3px;
    color: var(--paper-text);
  }
  .divider {
    position: absolute;
    left: 240px;
    top: 192px;
    width: 1px;
    height: 96px;
    background: var(--paper-text);
  }
  .contact-list {
    position: absolute;
    left: 256px;
    top: 204px;
    margin: 0;
    padding: 0;
    list-style: none;
    font-family: "Arimo", sans-serif;
    font-size: 11.5px;
    line-height: 16px;
    color: var(--paper-text);
  }
  .contact-list li { display: flex; align-items: center; gap: 7px; }
  .contact-icon { width: 10px; height: 10px; flex: none; }

  /* Picture side */
  .card--picture {
    background: linear-gradient(120deg, var(--photo-light) 0%, var(--photo-mid) 55%, var(--photo-dark) 100%);
  }
  .picture-fill { position: absolute; inset: 0; }
  .picture-name {
    position: absolute;
    left: 0;
    bottom: 70px;
    width: 100%;
    text-align: center;
    margin: 0;
    font-family: "Oswald", sans-serif;
    font-weight: 500;
    font-size: 50px;
    letter-spacing: 3px;
    color: var(--paper-text);
    text-transform: uppercase;
  }
</style>
</head>
<body>
<main class="canvas">

  <section class="card card--contact" aria-label="Contact side of card">
    <svg class="card__waves" viewBox="0 0 540 309" preserveAspectRatio="none" aria-hidden="true">
      <path d="M0 149 C 150 119, 290 124, 390 169 C 450 196, 500 212, 540 218 L540 309 L0 309 Z" fill="var(--band-light)"/>
      <path d="M0 157 C 150 127, 290 132, 390 177 C 450 204, 500 220, 540 226 L540 309 L0 309 Z" fill="var(--band-grey)"/>
      <path d="M0 165 C 150 135, 290 140, 390 185 C 450 212, 500 228, 540 234 L540 309 L0 309 Z" fill="var(--card-black)"/>
    </svg>
    <h1 class="brand-name">Marlow Thread</h1>
    <p class="holder-name">Karen Whitfield</p>
    <span class="divider"></span>
    <ul class="contact-list">
      <li>
        <svg class="contact-icon" viewBox="0 0 10 10"><rect width="10" height="10" rx="1.5" fill="var(--paper-text)"/><path d="M3 2.3 L4.3 3.6 L3.7 4.3 C4.1 5.2 4.8 5.9 5.7 6.3 L6.4 5.7 L7.7 7 L6.9 7.8 C4.6 7.6 2.4 5.4 2.2 3.1 Z" fill="var(--card-black)"/></svg>
        0498716204
      </li>
      <li>
        <svg class="contact-icon" viewBox="0 0 10 10"><rect width="10" height="10" rx="1.5" fill="var(--paper-text)"/><rect x="2" y="3" width="6" height="4" fill="none" stroke="var(--card-black)" stroke-width="0.9"/><path d="M2 3 L5 5.3 L8 3" fill="none" stroke="var(--card-black)" stroke-width="0.9"/></svg>
        info@marlowthread.example.au
      </li>
      <li>
        <svg class="contact-icon" viewBox="0 0 10 10"><rect width="10" height="10" rx="1.5" fill="var(--paper-text)"/><circle cx="5" cy="5" r="2.6" fill="none" stroke="var(--card-black)" stroke-width="0.9"/></svg>
        www.marlowthread.example.au
      </li>
      <li>
        <svg class="contact-icon" viewBox="0 0 10 10"><rect width="10" height="10" rx="1.5" fill="var(--paper-text)"/></svg>
        marlowthreadau
      </li>
      <li>
        <svg class="contact-icon" viewBox="0 0 10 10"><rect width="10" height="10" rx="1.5" fill="var(--paper-text)"/></svg>
        marlow_thread
      </li>
    </ul>
  </section>

  <section class="card card--picture">
    <div class="picture-fill" role="img" aria-label="Moody photograph of a woman surrounded by soft grey smoke"></div>
    <p class="picture-name">Marlow Thread</p>
  </section>

</main>
</body>
</html>
```